Business Cards for a law firm

Business cards for our law firm. Use our silhoette logo and OAK PARTNERS - check our website (www.oakpartners.example)

Contact Information for Business Card

our silhouette logo, OAK PARTNERS, 800-555-0147, Dorian Pemberton, dorian@oakpartners.example

Requirements
Must have
• our silhouette logo, OAK PARTNERS, 800-555-0147, Dorian Pemberton, dorian@oakpartners.example

```html
<!DOCTYPE html>
<html lang="en">
<head>
<meta charset="utf-8">
<title>Oak Partners — Business Card</title>
<link href="https://fonts.googleapis.com/css2?family=Montserrat:wght@400;600;700&display=swap" rel="stylesheet">
<style>
  :root {
    --navy: #22336b;
    --navy-soft: #2a3c78;
    --paper: #ffffff;
    --ink: #1a1a1a;
    --backdrop: #3b3b3b;
  }
  * { box-sizing: border-box; margin: 0; padding: 0; }
  html, body { width: 1200px; height: 1200px; overflow: hidden; }
  body {
    background: var(--backdrop);
    font-family: "Montserrat", sans-serif;
    display: flex;
    flex-direction: column;
    align-items: center;
    justify-content: center;
    gap: 52px;
  }
  .card {
    position: relative;
    width: 900px;
    height: 514px;
    border-radius: 34px;
    overflow: hidden;
  }

  /* Back side */
  .card--back { background: var(--navy); }
  .card--back .brand {
    position: absolute;
    left: 0; right: 0; top: 50%;
    transform: translateY(-50%);
    text-align: center;
    font-weight: 600;
    font-size: 64px;
    letter-spacing: 8px;
    color: var(--navy-soft);
  }

  /* Front side */
  .card--front { background: var(--paper); }
  .card--front .wave { position: absolute; inset: 0; }
  .card--front .brand {
    position: absolute;
    left: 56px; top: 124px;
    display: flex; align-items: center; gap: 14px;
    font-weight: 600;
    font-size: 34px;
    letter-spacing: 4px;
    color: var(--navy);
  }
  .brand__mark {
    width: 22px; height: 22px;
    background: var(--navy);
  }
  .person {
    position: absolute;
    right: 56px; top: 46px;
    text-align: right;
  }
  .person__name {
    font-weight: 700;
    font-size: 36px;
    color: var(--navy);
  }
  .person__role {
    font-size: 17px;
    color: var(--ink);
    margin-top: 2px;
  }
  .figures {
    position: absolute;
    left: 540px; top: 110px;
    width: 230px; height: 180px;
    border-radius: 40px;
    background: radial-gradient(ellipse at 50% 55%, rgba(34,51,107,0.85), rgba(34,51,107,0.15) 75%, rgba(34,51,107,0) 100%);
  }
  .contact {
    position: absolute;
    left: 130px; top: 228px;
    list-style: none;
    display: flex; flex-direction: column; gap: 10px;
    font-size: 21px;
    color: var(--ink);
  }
  .contact li { display: flex; align-items: center; gap: 12px; }
  .contact svg { width: 18px; height: 18px; fill: var(--navy); flex: none; }
</style>
</head>
<body>

  <section class="card card--back" aria-label="Card back">
    <div class="brand">OAK PARTNERS</div>
  </section>

  <section class="card card--front" aria-label="Card front">
    <svg class="wave" viewBox="0 0 900 514" preserveAspectRatio="none" aria-hidden="true">
      <path d="M0,514 L0,478 C200,392 420,368 600,352 C760,337 850,285 900,235 L900,514 Z" fill="var(--navy)"/>
      <path d="M60,462 C220,384 420,358 600,342 C760,327 845,277 900,224" fill="none" stroke="var(--navy)" stroke-width="2"/>
      <path d="M560,336 C720,320 830,274 880,222" fill="none" stroke="var(--navy)" stroke-width="2"/>
    </svg>

    <div class="brand"><span class="brand__mark"></span>OAK PARTNERS</div>

    <div class="person">
      <div class="person__name">Dorian Pemberton</div>
      <div class="person__role">Lawyer</div>
    </div>

    <div class="figures" role="img" aria-label="Illustration of two standing figures in silhouette"></div>

    <ul class="contact">
      <li>
        <svg viewBox="0 0 24 24"><path d="M6.6 10.8a15 15 0 0 0 6.6 6.6l2.2-2.2a1 1 0 0 1 1-.25 11.4 11.4 0 0 0 3.6.57 1 1 0 0 1 1 1V20a1 1 0 0 1-1 1A17 17 0 0 1 3 4a1 1 0 0 1 1-1h3.5a1 1 0 0 1 1 1c0 1.25.2 2.450.57 3.57a1 1 0 0 1-.25 1z"/></svg>
        800-555-0147
      </li>
      <li>
        <svg viewBox="0 0 24 24"><path d="M2 5h20v14H2z"/><path d="M3 6l9 7 9-7" fill="none" stroke="#fff" stroke-width="1.5"/></svg>
        dorian@oakpartners.example
      </li>
      <li>
        <svg viewBox="0 0 24 24"><circle cx="12" cy="12" r="10"/><path d="M2 12h20M12 2c3 3 3 17 0 20M12 2c-3 3-3 17 0 20" fill="none" stroke="#fff" stroke-width="1.3"/></svg>
        www.oakpartners.example
      </li>
    </ul>
  </section>

</body>
</html>
```